Album Cover for upcoming release

Hi, I need an album cover for a song that I’ll be releasing soon. The album cover must contain the title of the song, which is:

Carry the Moon (remix)

The album cover must also contain the artist name:

Owen Tarrick

The song is a remix of a song that I released in late-May called “Carry the Moon.” I wrote the original song for my wife. If you’re interested, please give it a listen on Velvo Tunes or Rumblewave under the artist Owen Tarrick. Here’s a Rumblewave link to the original song (it already has more than 175,000 streams):

https://play.rumblewave.example/track/7RbTqZ82KXN3pLmWcVoHeF?si=ztGd4NfQxWYb9uRsEoPaMc

The remix is VERY, VERY different! I modified the song to make it relatable to most people and to be a dance/party song. Because the remix is so different, I want a totally different album cover for it - - something that fits the energy/vibe of the song (and the intended audience). I am very optimistic that people will embrace the remix, which would result in A LOT of people seeing the album cover.

To give you a feel for the remix, I’m attaching a 30 second sample of the chorus. Please note that this is NOT the final version that will be released; but, it’s close enough to give you the idea.

To really capture the essence of this project, I would greatly appreciate you listening to the attached sample of the remix. Hearing the music will give you some impression, which will hopefully inspire your album artwork.

Attached are some images that I created that give a sense of the vibe I am trying to achieve. Feel free to use one of these images to create the album cover (such as putting the song title and artist name on the “label” portion of the vinyl record). But, you are NOT required to use one os these images.
Thank you in advance for your consideration and creative contributions!

Target Market(s)

Dance and party crowd; night clubs, sporting events, weddings

Font styles to use
Sans Serif

Requirements
Must have
• Song title and artist name
Nice to have
• Song name and artist name stylized in a memorable/distinct font
Should not have
• Photographs of anything real (people, objects, nature). Animated can be fine

```html
<!DOCTYPE html>
<html lang="en">
<head>
<meta charset="utf-8">
<title>Carry the Moon (Remix) – Owen Tarrick</title>
<link rel="stylesheet" href="https://fonts.googleapis.com/css2?family=Cabin+Sketch:wght@400&family=Archivo+Black&display=swap">
<style>
  :root {
    --glow-core: #fff3a6;
    --glow-gold: #ffc61f;
    --glow-orange: #ff6a1f;
    --glow-magenta: #d23c8e;
    --glow-cyan: #36cdf0;
    --glow-blue: #1f62d8;
    --glow-deep: #2b1f86;
    --title-yellow: #ffe81a;
    --title-white: #ffffff;
    --shadow: rgba(10, 10, 40, 0.75);
  }
  html, body {
    margin: 0;
    padding: 0;
    width: 1200px;
    height: 1200px;
    overflow: hidden;
    background: var(--glow-deep);
  }
  .cover {
    position: relative;
    width: 1200px;
    height: 1200px;
    overflow: hidden;
  }
  .cover-art {
    position: absolute;
    inset: 0;
    background: radial-gradient(ellipse 75% 70% at 50% 58%,
      var(--glow-core) 0%,
      var(--glow-gold) 16%,
      var(--glow-orange) 32%,
      var(--glow-magenta) 46%,
      var(--glow-cyan) 62%,
      var(--glow-blue) 80%,
      var(--glow-deep) 100%);
  }
  .title {
    position: absolute;
    top: 84px;
    left: 0;
    width: 1200px;
    margin: 0;
    text-align: center;
    font-family: "Cabin Sketch", sans-serif;
    font-weight: 400;
    font-size: 80px;
    line-height: 1;
    letter-spacing: 2px;
    text-transform: uppercase;
    text-shadow: 3px 4px 6px var(--shadow);
    white-space: nowrap;
  }
  .title-song { color: var(--title-yellow); }
  .title-version { color: var(--title-white); }
  .artist {
    position: absolute;
    top: 1020px;
    left: 0;
    width: 1200px;
    margin: 0;
    padding-left: 20px;
    box-sizing: border-box;
    text-align: center;
    font-family: "Archivo Black", sans-serif;
    font-size: 44px;
    line-height: 1;
    letter-spacing: 20px;
    color: var(--title-white);
    text-transform: uppercase;
    text-shadow: 2px 3px 5px var(--shadow);
    white-space: nowrap;
  }
</style>
</head>
<body>
  <main class="cover">
    <div class="cover-art" role="img" aria-label="Illustration of a glowing vinyl record set against a sunset over the sea, with bursting blue and cyan light rays"></div>
    <h1 class="title"><span class="title-song">Carry the Moon</span> <span class="title-version">(Remix)</span></h1>
    <p class="artist">Owen Tarrick</p>
  </main>
</body>
</html>
```